Business card for my new company (Accounting firm)

I need a business card for my new business Brightwell Advisory and Ledger SA. Our services are accounting, tax, audit and financial management. Our customers are small companies, start-ups and new companies. The final design has to show financial security, trust and growth. Please find our logo attached to the business card. Text for the business card: Brightwell Advisory and Ledger SA Tomas Varenholt Director and Founder Certified Accountant Tel. 022 418 57 34 tv@clairevalconseil.ch www.clairevalconseil.ch Rue des Vergières 27 1201 Geneva
Target Market(s)
Our customers are small companies, start-ups and new companies.
Industry/Entity Type
Finance And Accounting
Contact Information for Business Card
Claireval Conseil et Comptes SA
Tomas Varenholt
Directeur et Fondateur
Expert-comptable diplômé
Tél. 022 418 57 34
tv@clairevalconseil.ch
www.clairevalconseil.ch
Rue des Vergières 27
1201 Genève

```html
<!DOCTYPE html>
<html lang="fr">
<head>
<meta charset="utf-8">
<title>Claireval Conseil et Comptes SA – Carte de visite</title>
<link href="https://fonts.googleapis.com/css2?family=Roboto+Condensed:wght@400;700&display=swap" rel="stylesheet">
<style>
  :root {
    --bg: #2b2b2d;
    --white: #ffffff;
    --ink: #3a3f45;
    --sky: #35ade0;
    --azure: #2488c8;
    --navy: #1a6596;
    --back: #1b6494;
  }
  * { box-sizing: border-box; margin: 0; padding: 0; }
  html, body {
    width: 1200px; height: 960px; overflow: hidden;
    background: var(--bg);
    font-family: "Roboto Condensed", Arial, sans-serif;
  }
  .stage { position: relative; width: 1200px; height: 960px; }

  .card { position: absolute; box-shadow: 0 10px 30px rgba(0,0,0,.45); overflow: hidden; }

  /* Front */
  .card-front { left: 40px; top: 266px; width: 700px; height: 428px; background: var(--white); }
  .brand {
    position: absolute; left: 0; right: 0; top: 92px;
    display: flex; justify-content: center; align-items: center; gap: 14px;
  }
  .brand-mark { width: 30px; height: 30px; background: var(--sky); }
  .brand-name { font-size: 54px; font-weight: 700; color: var(--ink); letter-spacing: 4px; }

  .info-band { position: absolute; left: 0; right: 0; top: 262px; height: 112px; display: flex; }
  .info-band > div { padding: 18px 22px; color: var(--white); display: flex; flex-direction: column; justify-content: center; }
  .person { width: 37%; background: var(--sky); }
  .person-name { font-size: 27px; font-weight: 700; line-height: 1.05; }
  .person-role { font-size: 18px; line-height: 1.2; }
  .address { width: 31%; background: var(--navy); font-size: 17px; line-height: 1.3; }
  .contact { width: 32%; background: var(--azure); font-size: 16.5px; line-height: 1.45; }
  .contact-line { display: flex; align-items: center; gap: 8px; white-space: nowrap; }
  .contact-line svg { width: 13px; height: 13px; flex: none; fill: var(--white); }
  .base-rule { position: absolute; left: 0; right: 0; top: 390px; height: 5px; background: var(--azure); }

  /* Back */
  .card-back { left: 760px; top: 352px; width: 400px; height: 257px; background: var(--back); }
  .back-brand {
    position: absolute; left: 0; right: 0; top: 88px;
    display: flex; justify-content: center; align-items: center; gap: 10px;
  }
  .back-brand .brand-mark { width: 20px; height: 20px; background: var(--sky); }
  .back-brand .brand-name { font-size: 36px; color: var(--white); letter-spacing: 3px; }
  .back-web {
    position: absolute; left: 0; right: 0; top: 150px; text-align: center;
    font-size: 13px; color: var(--white); letter-spacing: 3px;
  }
</style>
</head>
<body>
<main class="stage">
  <section class="card card-front" aria-label="Recto de la carte">
    <div class="brand">
      <span class="brand-mark"></span>
      <span class="brand-name">CLAIREVAL</span>
    </div>
    <div class="info-band">
      <div class="person">
        <p class="person-name">Tomas Varenholt</p>
        <p class="person-role">Directeur et Fondateur</p>
        <p class="person-role">Expert-comptable diplômé</p>
      </div>
      <div class="address">
        <p>Claireval Conseil et Comptes SA</p>
        <p>Rue des Vergières 27</p>
        <p>1201 Genève</p>
      </div>
      <div class="contact">
        <p class="contact-line">
          <svg viewBox="0 0 24 24"><path d="M6.6 10.8a15.1 15.1 0 0 0 6.6 6.6l2.2-2.2a1 1 0 0 1 1-.25 11.4 11.4 0 0 0 3.6.57 1 1 0 0 1 1 1V20a1 1 0 0 1-1 1A17 17 0 0 1 3 4a1 1 0 0 1 1-1h3.5a1 1 0 0 1 1 1c0 1.25.2 2.45.57 3.57a1 1 0 0 1-.25 1z"/></svg>
          022 418 57 34
        </p>
        <p class="contact-line">
          <svg viewBox="0 0 24 24"><path d="M2 5h20v14H2zm2 2v.4l8 5 8-5V7zm0 2.8V17h16V9.8l-8 5z"/></svg>
          tv@clairevalconseil.ch
        </p>
        <p class="contact-line">
          <svg viewBox="0 0 24 24"><path d="M12 2a10 10 0 1 0 0 20 10 10 0 0 0 0-20zm-1 17.9A8 8 0 0 1 4.2 10.5L9 15v1a2 2 0 0 0 2 2zm6.9-2.5A2 2 0 0 0 16 16h-1v-3a1 1 0 0 0-1-1H8v-2h2a1 1 0 0 0 1-1V7h2a2 2 0 0 0 2-2v-.4a8 8 0 0 1 2.9 12.8z"/></svg>
          www.clairevalconseil.ch
        </p>
      </div>
    </div>
    <div class="base-rule"></div>
  </section>

  <section class="card card-back" aria-label="Verso de la carte">
    <div class="back-brand">
      <span class="brand-mark"></span>
      <span class="brand-name">CLAIREVAL</span>
    </div>
    <p class="back-web">www.clairevalconseil.ch</p>
  </section>
</main>
</body>
</html>
```